Camp Thornbrook 2021 Magazine Design

We are for someone to design our annual magazine/newsletter. This is a print newsletter that is a total of 20 pages. It will need to be designed in a way that is easy to share with our printers. The designer will need to be someone who is creative and easy to work with.
For those interested in this project we ask that you design 4 to 6 pages for us to view. Once we select the designer we will want the rest created in a two-week time span. For those submitting a bid please include front cover, theme & dates, mission & vision, and Make the Difference.

This link will provide the layout of the newsletter https://files.parcelvault.example/doc/7qzRk2LmVt9XwPa4NbHc6DsYe3FuJg8KoTiW5rQx/edit?share=1.

This link will provide you with the pictures that are needed and a few documents https://files.parcelvault.example/folders/4TpWx8QnRb2ZyLc7MfVd5HsJ?share=1

Details:
20 pages long (including covers)
8.5 x 11

Please message me if you need any further details.

Target Market(s)

Our alumni base. Covers all ages

Requirements
Must have
• Spelled out in document
Nice to have
• Spelled out in document
Should not have
• Spelled out in document

```html
<!DOCTYPE html>
<html lang="en">
<head>
<meta charset="utf-8">
<title>Camp Thornbrook 2021 Magazine – Contents and Make the Difference</title>
<link rel="stylesheet" href="https://fonts.googleapis.com/css2?family=Abril+Fatface&family=Barlow:wght@300;400;600&display=swap">
<style>
  :root {
    --green: #0e6b47;
    --green-deep: #0a5638;
    --gold: #e6c41c;
    --ink: #4f4f4f;
    --ink-soft: #6a6a6a;
    --paper: #ffffff;
    --column: #f1f1f0;
    --stage: #ececec;
  }
  * { box-sizing: border-box; margin: 0; padding: 0; }
  html, body { width: 1200px; height: 880px; overflow: hidden; }
  body {
    background: var(--stage);
    font-family: "Barlow", Arial, sans-serif;
    color: var(--ink);
  }
  .spread {
    position: absolute;
    left: 13px; top: 60px;
    width: 1174px; height: 760px;
    display: flex;
    box-shadow: 0 8px 30px rgba(0,0,0,.18);
  }
  .page { position: relative; width: 587px; height: 760px; overflow: hidden; background: var(--paper); }

  /* Left page: contents */
  .contents-photo {
    position: absolute; inset: 0;
    background:
      linear-gradient(180deg, rgba(255,255,255,0) 30%, rgba(244,244,240,.85) 62%, #f2f1ec 100%),
      linear-gradient(160deg, #3f6a2e 0%, #5f8a45 30%, #7d8a6a 55%, #a49a86 80%, #c9c2b4 100%);
  }
  .contents-banner {
    position: absolute; left: 40px; top: 405px;
    width: 500px; height: 96px;
  }
  .contents-banner .frame {
    position: absolute; left: 14px; top: -10px; right: -12px; bottom: 10px;
    border: 2px solid var(--gold);
  }
  .contents-banner .band {
    position: absolute; inset: 0;
    background: var(--green);
    display: flex; align-items: center; justify-content: center;
  }
  .contents-banner h2 {
    font-family: "Abril Fatface", Georgia, serif;
    font-weight: 400;
    font-size: 50px; color: var(--paper); letter-spacing: .5px;
  }
  .contents-list {
    position: absolute; left: 48px; right: 40px; top: 530px;
    list-style: none;
  }
  .contents-list li {
    display: flex; align-items: flex-end; gap: 10px;
    height: 21px;
    font-size: 14px; font-weight: 600; color: var(--ink-soft);
  }
  .contents-list .rule { flex: 1; border-bottom: 1px solid var(--green); margin-bottom: 5px; }
  .contents-list .pages { font-size: 12px; font-weight: 600; color: var(--ink-soft); white-space: nowrap; }

  /* Right page: Make the Difference */
  .article-column {
    position: absolute; left: 0; top: 0; bottom: 0; width: 300px;
    background: var(--column);
    padding: 42px 22px 30px 30px;
  }
  .article-column h1 {
    font-family: "Abril Fatface", Georgia, serif;
    font-weight: 400;
    color: var(--green); font-size: 38px; line-height: 1.02;
    margin-bottom: 22px;
  }
  .article-column p {
    font-size: 8.4px; line-height: 1.38; font-weight: 300; color: #444;
    text-align: justify; margin-bottom: 10px;
  }
  .article-photo {
    position: absolute; left: 300px; top: 0; right: 0; bottom: 0;
    background: linear-gradient(170deg, #6f9a4e 0%, #8fb067 30%, #7a8f86 60%, #5d7185 100%);
  }
  .folio {
    position: absolute; right: 14px; bottom: 16px;
    width: 24px; height: 18px;
    border: 1px solid var(--gold);
    background: var(--green);
    color: var(--paper); font-size: 9px; font-weight: 400;
    display: flex; align-items: center; justify-content: center;
  }
  .gutter {
    position: absolute; left: 577px; top: 0; width: 20px; height: 760px;
    background: linear-gradient(90deg, rgba(0,0,0,0), rgba(0,0,0,.12) 50%, rgba(0,0,0,0));
    pointer-events: none;
  }
</style>
</head>
<body>
<main class="spread">
  <section class="page page--contents">
    <div class="contents-photo" role="img" aria-label="Wooded camp trail with a carved wooden cross post, fading to white at the bottom"></div>
    <div class="contents-banner">
      <div class="frame"></div>
      <div class="band"><h2>Table of Contents</h2></div>
    </div>
    <ol class="contents-list">
      <li><span>Make the Difference</span><span class="rule"></span><span class="pages">Page 3</span></li>
      <li><span>Golf Tournament</span><span class="rule"></span><span class="pages">Pages 4 &amp; 5</span></li>
      <li><span>2021 Theme and Dates</span><span class="rule"></span><span class="pages">Pages 6 &amp; 7</span></li>
      <li><span>Where Are They Now: Dale Hartwell</span><span class="rule"></span><span class="pages">Pages 8 &amp; 9</span></li>
      <li><span>2019 Donors</span><span class="rule"></span><span class="pages">Pages 10, 11, &amp; 12</span></li>
      <li><span>2019 Thornbrook Awards</span><span class="rule"></span><span class="pages">Page 13</span></li>
      <li><span>Bee Rock</span><span class="rule"></span><span class="pages">Pages 14 &amp; 15</span></li>
      <li><span>Mission/Vision</span><span class="rule"></span><span class="pages">Pages 16 &amp; 17</span></li>
      <li><span>A Place We Call Home</span><span class="rule"></span><span class="pages">Page 18</span></li>
      <li><span>Memorials</span><span class="rule"></span><span class="pages">Page 19</span></li>
    </ol>
  </section>

  <section class="page page--article">
    <div class="article-column">
      <h1>Make the<br>Difference</h1>
      <p>To say that 2020 has been a challenging year is a huge understatement! March 2020 is a month none of us will soon forget. Just as we were getting ready to ramp up for the summer, things began to shut down all around us. At first we hoped it would just be a few weeks only impacting our spring retreats, but as the spring progressed, it soon became evident our 2020 summer was being threatened.</p>
      <p>In late May, we made the difficult decision to cancel all summer events. For the first time in 73 years, there would be no summer camp at Thornbrook. Our summer programming is at the heart of what we do and who we are. From the very beginning, Thornbrook's main mission has been to share Christ through the summer camp program.</p>
      <p>After dealing with the emotional aspect of not having camp this summer, we had to look at the reality of the financial impact canceling the summer would have on Thornbrook. Over 50% of our annual revenue comes from our summer programming and summer rentals. We also had to take into account the loss of our spring rentals and the possibility of fall rentals canceling. While we were confident God would provide for Thornbrook, as He always has, we weren't sure how this would take place.</p>
      <p>We determined that even with drastically cutting expenses, we would need an additional $50,000 to make up for the lost revenue. In late June, we received a phone call from one of our long-time Thornbrook families who was interested in helping us through this difficult time. They generously pledged $10,000 as a matching gift to help motivate the Thornbrook family to give as well. In early July, we announced the "Make the Difference" fundraising campaign. Our initial goal was to raise $10,000 in one week to receive the matching gift with the hope of substantially reducing the $50,000 deficit.</p>
      <p>The Thornbrook family showed their love and dedication through their extraordinary generosity. By the end of Monday, the first day of the campaign, we had exceeded our initial goal of $10,000 ensuring the matching gift. By the end of the week, over $64,000 was raised!</p>
      <p>While 2020 has not been the year we had hoped for, it has been a year in which Thornbrook has been blessed beyond expectations!</p>
    </div>
    <div class="article-photo" role="img" aria-label="Camp counselor hugging two smiling young campers outdoors among green trees"></div>
    <div class="folio">03</div>
  </section>
  <div class="gutter"></div>
</main>
</body>
</html>
```